Tall Fern Roofing Business Card

Need a business card with the logo that was designed here

Contact Information for Business Card

Name, Title, Phone, Email, Website, Company name

```html
<!DOCTYPE html>
<html lang="en">
<head>
<meta charset="utf-8">
<title>Tall Fern Roofing Business Card</title>
<link href="https://fonts.googleapis.com/css2?family=Open+Sans:wght@400;600;700&display=swap" rel="stylesheet">
<style>
  :root {
    --backdrop: #323232;
    --brand-blue: #1176c0;
    --brand-blue-deep: #0f63a8;
    --roof-gray: #939598;
    --ink: #1a1a1a;
    --paper: #ffffff;
  }
  * { margin: 0; padding: 0; box-sizing: border-box; }
  html, body {
    width: 1200px;
    height: 780px;
    overflow: hidden;
    background: var(--backdrop);
    font-family: "Open Sans", sans-serif;
  }
  .canvas {
    position: relative;
    width: 1200px;
    height: 780px;
    display: flex;
    align-items: center;
    justify-content: center;
    gap: 40px;
  }
  .card {
    position: relative;
    width: 540px;
    height: 309px;
    overflow: hidden;
  }

  /* Back side */
  .card-back {
    background: var(--brand-blue);
    display: flex;
    align-items: center;
    justify-content: center;
  }
  .card-back .brand-name {
    font-weight: 700;
    font-size: 40px;
    color: var(--brand-blue-deep);
    letter-spacing: 0.5px;
    display: flex;
    align-items: center;
    gap: 14px;
  }
  .brand-square {
    display: inline-block;
    width: 22px;
    height: 22px;
    background: currentColor;
  }

  /* Front side */
  .card-front {
    background: var(--paper);
  }
  .front-logo {
    position: absolute;
    left: 34px;
    top: 58px;
    font-weight: 700;
    font-size: 27px;
    color: var(--brand-blue);
    display: flex;
    align-items: center;
    gap: 10px;
  }
  .front-logo .brand-square { width: 16px; height: 16px; }
  .holder {
    position: absolute;
    right: 34px;
    top: 26px;
    text-align: right;
  }
  .holder-name {
    font-weight: 700;
    font-size: 30px;
    line-height: 1.1;
  }
  .holder-name .first { color: var(--brand-blue); }
  .holder-name .last { color: var(--roof-gray); }
  .holder-title {
    font-weight: 600;
    font-size: 15px;
    color: var(--ink);
  }
  .edge-bar {
    position: absolute;
    right: 0;
    top: 22px;
    width: 14px;
    height: 58px;
    background: var(--brand-blue);
  }
  .contact-band {
    position: absolute;
    left: 0;
    bottom: 0;
    width: 540px;
    height: 150px;
  }
  .contact-list {
    position: absolute;
    left: 30px;
    bottom: 26px;
    list-style: none;
    color: var(--paper);
    font-size: 15px;
    line-height: 1.45;
  }
  .contact-list li { display: flex; align-items: center; gap: 8px; }
  .contact-list .address { padding-left: 0; }
  .contact-list .icon { width: 14px; height: 14px; flex: none; }
  .contact-list .spacer { height: 6px; }
</style>
</head>
<body>
<main class="canvas">

  <section class="card card-back" aria-label="Card back">
    <div class="brand-name"><span class="brand-square"></span>Tall Fern Roofing</div>
  </section>

  <section class="card card-front" aria-label="Card front">
    <div class="front-logo"><span class="brand-square"></span>Tall Fern Roofing</div>

    <div class="edge-bar"></div>
    <div class="holder">
      <div class="holder-name"><span class="first">Dale</span> <span class="last">Merritt</span></div>
      <div class="holder-title">Managing Director</div>
    </div>

    <svg class="contact-band" viewBox="0 0 540 150" aria-hidden="true">
      <polygon points="0,40 330,40 270,150 0,150" fill="var(--brand-blue)"/>
      <line x1="0" y1="138" x2="540" y2="138" stroke="var(--paper)" stroke-width="3"/>
      <rect x="0" y="141" width="540" height="9" fill="var(--brand-blue)"/>
    </svg>

    <ul class="contact-list">
      <li class="address">1840 Cedar Hollow Rd. Suite 300</li>
      <li class="address">Millbrook, TX 75520</li>
      <li>
        <svg class="icon" viewBox="0 0 16 16"><path d="M4 1l3 3-2 2c1 2 3 4 5 5l2-2 3 3-2 3C7 15 1 9 1 3z" fill="#fff"/></svg>
        (555) 214-6083
      </li>
      <li>
        <svg class="icon" viewBox="0 0 16 16"><rect x="1" y="3" width="14" height="10" fill="none" stroke="#fff" stroke-width="1.6"/><path d="M1 3l7 6 7-6" fill="none" stroke="#fff" stroke-width="1.6"/></svg>
        info@website.com
      </li>
      <li>
        <svg class="icon" viewBox="0 0 16 16"><circle cx="8" cy="8" r="6.5" fill="none" stroke="#fff" stroke-width="1.5"/><path d="M1.5 8h13M8 1.5c-3 3-3 10 0 13M8 1.5c3 3 3 10 0 13" fill="none" stroke="#fff" stroke-width="1.2"/></svg>
        www.website.com
      </li>
    </ul>
  </section>

</main>
</body>
</html>
```